Hong Kong based International Remittance and ForEx company requires website design

We need a website designed for a new European - Hong Kong based ForEx & fund remittence entity.

The company specialises in larger corporate & high net worth private client trades, therefore the design must aesthetically reflect this (sophisticated). As a theme colour, financial entities tend to use either blue or red; if blue, our preference is a darker blue. Visually, our preference is less copy, more imagery.

Number of pages would be limited; landing (home), about us, client registration (x1 Corporate form, x1 Private Client form), Contact Us.

Have uploaded the existing logo - please note this is to be redesigned, although the colour scheme will remain the same. Please also note that copy will follow - please use Lorem Ipsum.

Target Market(s)

Medium to large Corporations. High net worth individuals.

Industry/Entity Type

Financial Service

Coding

Coded - Design and coding required

Number of Pages Required

4 page

Font styles to use
Serif

Requirements
Nice to have
• ForEx ticker,

```html
<!DOCTYPE html>
<html lang="en">
<head>
<meta charset="utf-8">
<title>Harbourline Incorporation Limited</title>
<link rel="stylesheet" href="https://fonts.googleapis.com/css2?family=Gentium+Book+Plus:wght@400;700&display=swap">
<style>
:root{
  --red:#d30d0d;
  --red-dark:#b70909;
  --ink:#222;
  --grey:#777;
  --line:#e2e2e2;
  --black:#0c0c0c;
  --footer:#141414;
  --white:#fff;
  --serif:"Gentium Book Plus", Georgia, serif;
}
*{margin:0;padding:0;box-sizing:border-box}
html,body{width:1200px;height:2449px;overflow:hidden}
body{font-family:var(--serif);color:var(--ink);background:var(--white);position:relative}

/* header */
.site-header{position:absolute;left:0;top:0;width:1200px;height:131px;background:var(--white)}
.brand-name{position:absolute;left:144px;top:44px;font-size:36px;line-height:1;color:var(--ink)}
.language{position:absolute;left:932px;top:26px;display:flex;align-items:center;gap:8px;font-size:9.5px;color:var(--red);letter-spacing:.5px}
.language-select{width:56px;height:30px;border:1px solid #ccc;border-radius:3px;font-size:10px;color:var(--ink);display:flex;align-items:center;justify-content:space-between;padding:0 7px}
.main-nav{position:absolute;top:72px;left:483px}
.main-nav a{font-size:12.5px;color:var(--ink);text-decoration:none;text-transform:uppercase;letter-spacing:.4px;position:absolute;white-space:nowrap}
.main-nav a.active{color:var(--red)}
.main-nav a.active::after{content:"";position:absolute;left:0;right:0;top:24px;height:2px;background:var(--red)}

/* hero */
.hero{position:absolute;left:0;top:131px;width:1200px;height:669px;
  background:linear-gradient(180deg,#3d86d6 0%,#8cbbea 30%,#dfe9f1 42%,#6f8fa6 55%,#5a6f80 64%,#2f5f8f 75%,#3e6fa0 100%)}
.hero-caption{position:absolute;left:0;bottom:0;width:1200px;height:103px;background:rgba(30,30,30,.62);display:flex;align-items:center;justify-content:center}
.hero-caption p{color:var(--white);font-size:26px;letter-spacing:.3px}
.hero-arrow{position:absolute;top:609px}

/* ticker */
.ticker{position:absolute;left:0;top:800px;width:1200px;height:64px;background:var(--white)}
.ticker-label{position:absolute;left:0;top:0;width:238px;height:64px;background:var(--black);color:var(--white);font-size:17px;letter-spacing:1px;display:flex;align-items:center;justify-content:center}
.ticker-item{position:absolute;top:23px;font-size:13.5px;color:var(--ink);white-space:nowrap}
.ticker-item .sym{color:var(--red-dark)}
.ticker-item .chg{color:var(--red);margin-left:14px}
.down{display:inline-block;width:0;height:0;border-left:5px solid transparent;border-right:5px solid transparent;border-top:8px solid var(--red);margin:0 3px}

/* welcome */
.welcome{position:absolute;left:0;top:864px;width:1200px;height:330px;background:var(--red)}
.welcome-photo{position:absolute;left:144px;top:55px;width:362px;height:222px;border:5px solid var(--white);
  background:linear-gradient(135deg,#d9d9d9 0%,#7a7a7a 40%,#1c1c1c 70%,#444 100%)}
.welcome h2{position:absolute;left:534px;top:48px;font-size:25px;font-weight:400;color:var(--white);letter-spacing:.8px}
.welcome-rule{position:absolute;left:534px;top:96px;width:521px;height:1px;background:rgba(255,255,255,.75)}
.welcome p{position:absolute;left:534px;top:122px;width:522px;color:var(--white);font-size:13.6px;line-height:28.6px}

/* expertise */
.expertise h2{position:absolute;left:0;top:1245px;width:1200px;text-align:center;font-size:25px;font-weight:400;letter-spacing:.6px}
.expertise-rule{position:absolute;left:144px;top:1295px;width:912px;height:1px;background:var(--line)}
.card{position:absolute;top:1324px;width:286px}
.card-photo{width:286px;height:185px;border:5px solid #e7e7e7}
.card h3{font-size:19px;font-weight:400;color:var(--red);margin-top:30px}
.card p{font-size:10.5px;line-height:19px;color:var(--grey);margin-top:20px;width:282px}

/* about */
.about{position:absolute;left:0;top:1751px;width:1200px;height:401px;
  background:linear-gradient(180deg,#2b2b2b 0%,#3a3a3a 55%,#555 78%,#2e2e2e 100%);color:var(--white)}
.about h2{position:absolute;left:0;top:100px;width:1200px;text-align:center;font-size:26px;font-weight:400;letter-spacing:1px}
.about p{position:absolute;left:144px;top:156px;width:912px;text-align:center;font-size:14px;line-height:24px}
.btn-outline{position:absolute;left:527px;top:290px;width:136px;height:44px;border:1px solid rgba(255,255,255,.85);color:var(--white);font-size:12.5px;letter-spacing:.4px;display:flex;align-items:center;justify-content:center;text-decoration:none}

/* footer */
.site-footer{position:absolute;left:0;top:2152px;width:1200px;height:242px;background:var(--footer)}
.footer-col{position:absolute;top:32px}
.footer-col h4{font-size:10.5px;font-weight:400;color:var(--red);text-transform:uppercase;letter-spacing:.5px;margin-bottom:14px}
.footer-col ul{list-style:none}
.footer-col li{font-size:10.5px;color:#cfcfcf;height:24px;padding-left:16px;position:relative;white-space:nowrap}
.footer-col li::before{content:"";position:absolute;left:2px;top:3px;border-top:4px solid transparent;border-bottom:4px solid transparent;border-left:5px solid #eee}
.bottom-bar{position:absolute;left:0;top:2394px;width:1200px;height:55px;background:#0a0a0a}
.copyright{position:absolute;left:109px;top:20px;font-size:10px;color:#bbb}
.social{position:absolute;left:968px;top:21px;display:flex;gap:14px}
.social span{width:11px;height:11px;border-radius:50%;background:#ddd;display:block}
.lang-code{position:absolute;left:1170px;top:19px;font-size:10px;color:#bbb}
</style>
</head>
<body>

<header class="site-header">
  <div class="brand-name">Harbourline</div>
  <div class="language">LANGUAGE : <span class="language-select">ENG
    <svg width="8" height="6" viewBox="0 0 8 6"><path d="M1 1l3 3 3-3" stroke="#222" stroke-width="1.5" fill="none"/></svg></span></div>
  <nav class="main-nav">
    <a class="active" style="left:0">About us</a>
    <a style="left:90px">International</a>
    <a style="left:219px">Payments</a>
    <a style="left:315px">Contact us</a>
    <a style="left:420px">Client</a>
    <a style="left:493px">Application</a>
  </nav>
</header>

<section class="hero" role="img" aria-label="Harbour skyline with a red-sailed junk boat under a blue sky">
  <svg class="hero-arrow" style="left:80px" width="18" height="26" viewBox="0 0 18 26"><path d="M15 3L5 13l10 10" stroke="#fff" stroke-width="4" fill="none"/></svg>
  <svg class="hero-arrow" style="left:1102px" width="18" height="26" viewBox="0 0 18 26"><path d="M3 3l10 10L3 23" stroke="#fff" stroke-width="4" fill="none"/></svg>
  <div class="hero-caption"><p>We are a new ForEx &amp; fund remittance entity based in European - Hong Kong</p></div>
</section>

<section class="ticker">
  <div class="ticker-label">FOREX TICKER</div>
  <div class="ticker-item" style="left:304px"><span class="sym">TECH 100</span>&nbsp; $ 16,78 <span class="chg">0,31 <span class="down"></span> 1,81%</span></div>
  <div class="ticker-item" style="left:550px"><span class="sym">TREAS.</span>&nbsp;&nbsp;&nbsp; $ 16,78 <span class="chg">0,31 <span class="down"></span> 1,81%</span></div>
  <div class="ticker-item" style="left:826px"><span class="sym">BROAD 500</span>&nbsp; $ 16,78 <span class="chg">0,31 <span class="down"></span> 1,81%</span></div>
</section>

<section class="welcome">
  <div class="welcome-photo" role="img" aria-label="Black and white city skyline with a stock price board"></div>
  <h2>WELCOME TO HARBOURLINE</h2>
  <div class="welcome-rule"></div>
  <p>Harbourline Incorporation Limited is a regulated Money Service Operator Number (18-04-02265), licensed authorised by the Harbour Financial Licensing Office.We provide the international settlement and reconciliation of funds for and on behalf of our clients which include both corporates and individuals.As well as acting as a remittance entity we also provide foreign exchange services and work closely with our clients to source</p>
</section>

<section class="expertise">
  <h2>OUR EXPERTISE</h2>
  <div class="expertise-rule"></div>
  <article class="card" style="left:144px">
    <div class="card-photo" role="img" aria-label="Hands holding a tablet showing a financial chart" style="background:linear-gradient(135deg,#6e8fa8,#c9d4dc 50%,#3c4b58)"></div>
    <h3>International Money Transfer</h3>
    <p>Lorem Ipsum is simply dummy text of the printing and typesetting industry. Lorem Ipsum has been the industry's standard dummy text ever since the 1500s, when an unknown printer took a galley of type and scrambled it to make a type specimen book.</p>
  </article>
  <article class="card" style="left:456px">
    <div class="card-photo" role="img" aria-label="Businessman in a suit holding a tablet over a city view" style="background:linear-gradient(135deg,#e9ecef,#b8c3cc 50%,#5d6b78)"></div>
    <h3>Foreign Exchange</h3>
    <p>Lorem Ipsum is simply dummy text of the printing and typesetting industry. Lorem Ipsum has been the industry's standard dummy text ever since the 1500s, when an unknown printer took a galley of type and scrambled it to make a type specimen book.</p>
  </article>
  <article class="card" style="left:764px">
    <div class="card-photo" role="img" aria-label="Person at a laptop reviewing printed charts on a desk" style="background:linear-gradient(135deg,#f4efe9,#d9dde3 55%,#8fa4bd)"></div>
    <h3>Paying &amp; Receiving Agency</h3>
    <p>Lorem Ipsum is simply dummy text of the printing and typesetting industry. Lorem Ipsum has been the industry's standard dummy text ever since the 1500s, when an unknown printer took a galley of type and scrambled it to make a type specimen book.</p>
  </article>
</section>

<section class="about" role="img" aria-label="Dark monochrome harbour skyline behind the about section">
  <h2>ABOUT US</h2>
  <p>Harbourline is a leading provider of international payment services and foreign exchange to corporations and individuals covering most of the world including; throughout Asia, South America, and Europe.We engage with our clients with unmatched personalised service and aim to establish longevity with all our client relationships. Coupled with our excellent customer service, highly competitive rates and in depth market knowledge we provide a simple, reliable and cost effective service to all of our clients.</p>
  <a class="btn-outline">CONTACT US</a>
</section>

<footer class="site-footer">
  <div class="footer-col" style="left:109px">
    <h4>About us</h4>
    <ul><li>Our Ethos</li><li>Affiliates</li><li>FAQ's</li></ul>
  </div>
  <div class="footer-col" style="left:312px">
    <h4>International payments</h4>
    <ul><li>Making Payments</li><li>Customer Protection</li><li>NoObligation</li><li>Corporate &nbsp;&nbsp; Clients</li><li>Private Clients</li></ul>
  </div>
  <div class="footer-col" style="left:612px">
    <h4>Client application</h4>
    <ul><li>Private Client</li><li>Corporate &nbsp;&nbsp; Client</li></ul>
  </div>
  <div class="footer-col" style="left:892px">
    <h4>Company</h4>
    <ul><li>Terms&amp;Conditions</li><li>Peace of Mind</li><li>Data &nbsp; Protection &nbsp; &amp;Privacy</li><li>AntiMoneyLaundering</li><li>Legal</li><li>Contact Us</li></ul>
  </div>
</footer>

<div class="bottom-bar">
  <div class="copyright">© 2016 Harbourline Incorporation</div>
  <div class="social" aria-label="Social links"><span></span><span></span><span></span><span></span></div>
  <div class="lang-code">cs</div>
</div>

</body>
</html>
```